Stonebrace Business Card Design

The Stonebrace Co is an aggregate (crushing) equipment dealer serving Western Canadian provinces. Stonebrace is a distributor of aggregate equipment for different manufacturers.

We are looking to change and update the existing business card which has been used since the existence of the company. A copy of existing card has been attached for reference. The Stonebrace Co logo we want to remain the same and we want the green color to remain the same.

We are wanting something new with a different look. A refreshing card to show a new modern and updated look. No longer wanting to have the manufacturers on the back of the card but something more like our logo on the back of the card with a statement like "Crushing Solutions"

ideas could be:
- card can be different colors on front and back
- front or reverse of the card could possibly be the green color with the logo in black

Target Market(s)

Owners of Aggregate/Crushing companies

Contact Information for Business Card

see above

Requirements
Must have
• - logo to remain same along with same font within logo
• - green color to remain same
Nice to have
• as noted above under project description
Should not have

```html
<!DOCTYPE html>
<html lang="en">
<head>
<meta charset="utf-8">
<title>The Stonebrace Co — Business Card</title>
<link rel="stylesheet" href="https://fonts.googleapis.com/css2?family=Roboto:wght@400;500;700&family=Roboto+Condensed:wght@700&family=Archivo:wght@700&display=swap">
<style>
  :root {
    --backdrop: #5a4838;
    --card-white: #f3f3f3;
    --brand-green: #8a8b06;
    --ink: #231f20;
    --text-grey: #4a4a4a;
    --rule-grey: #cfcfcf;
    --faint-grey: #e4e4e4;
  }
  * { margin: 0; padding: 0; box-sizing: border-box; }
  html, body {
    width: 1200px; height: 960px; overflow: hidden;
    background: var(--backdrop);
  }
  .card {
    position: absolute;
    width: 600px; height: 343px;
    border-radius: 18px;
    overflow: hidden;
  }
  .card--front { left: 314px; top: 113px; background: var(--card-white); }
  .card--back { left: 311px; top: 472px; background: var(--brand-green); }

  .faint-pattern {
    position: absolute; left: 250px; top: 0; width: 350px; height: 343px;
    background: radial-gradient(ellipse at 70% 55%, var(--faint-grey) 0%, rgba(228,228,228,0) 70%);
  }
  .brand-dot {
    position: absolute; left: 146px; top: 120px;
    width: 72px; height: 72px; border-radius: 50%;
    background: var(--brand-green);
  }
  .back-shape {
    position: absolute; left: 300px; top: 10px;
    width: 330px; height: 330px; border-radius: 50%;
    background: var(--ink);
  }

  .wordmark {
    position: absolute;
    font-family: "Archivo", "Helvetica Neue", Arial, sans-serif;
    font-weight: 700;
    color: var(--ink);
    white-space: nowrap;
    letter-spacing: 0.2px;
  }
  .card--front .wordmark { left: 58px; top: 222px; font-size: 21.5px; }
  .card--back .wordmark { left: 22px; top: 271px; font-size: 20px; }

  .tagline {
    position: absolute; left: 69px; top: 296px;
    font-family: "Roboto", Arial, sans-serif;
    font-weight: 500; font-size: 16px; color: var(--ink);
  }

  .contact { position: absolute; left: 363px; top: 70px; width: 190px; }
  .contact__name {
    font-family: "Roboto Condensed", "Arial Narrow", sans-serif;
    font-weight: 700; font-size: 21px; line-height: 24px;
    color: var(--brand-green);
  }
  .contact__title {
    font-family: "Roboto", Arial, sans-serif;
    font-weight: 500; font-size: 15px; line-height: 20px;
    color: var(--ink);
  }
  .rule { height: 1px; margin: 9px 0 10px; background: var(--rule-grey); width: 163px; }
  .rule--green { background: var(--brand-green); width: 188px; opacity: .7; margin: 9px 0 9px; }
  .contact__address, .contact__list {
    font-family: "Roboto", Arial, sans-serif;
    font-size: 14px; line-height: 18px; color: var(--text-grey);
  }
  .contact__list { list-style: none; }
  .contact__list li { display: flex; align-items: center; height: 19.3px; }
  .contact__list svg { width: 13px; height: 13px; margin: 0 10px 0 1px; fill: var(--brand-green); flex: none; }
</style>
</head>
<body>
  <section class="card card--front" aria-label="Card front">
    <div class="faint-pattern" role="img" aria-label="Faint brand pattern in light grey"></div>
    <div class="brand-dot"></div>
    <div class="wordmark">THE STONEBRACE CO.</div>
    <div class="contact">
      <div class="contact__name">DALE MERCER</div>
      <div class="contact__title">CEO/FOUNDER</div>
      <div class="rule"></div>
      <address class="contact__address" style="font-style:normal">2210- 48B Avenue<br>Leduc, Alberta T9E 5K1</address>
      <div class="rule rule--green"></div>
      <ul class="contact__list">
        <li><svg viewBox="0 0 16 16" aria-hidden="true"><path d="M3.5 1l3 3-1.6 2a9 9 0 0 0 5.1 5.1l2-1.6 3 3-2 2.5C6.5 15 1 9.5.9 3z"/></svg>780.555.0142</li>
        <li><svg viewBox="0 0 16 16" aria-hidden="true"><path d="M4 0h8a1 1 0 0 1 1 1v14a1 1 0 0 1-1 1H4a1 1 0 0 1-1-1V1a1 1 0 0 1 1-1zm1 2v10h6V2zm3 11a1 1 0 1 0 0 2 1 1 0 0 0 0-2z"/></svg>780.555.0187</li>
        <li><svg viewBox="0 0 16 16" aria-hidden="true"><path d="M4 1h8v4H4zM1 6h14v7h-3v2H4v-2H1zm4 5v3h6v-3z"/></svg>780.555.0163</li>
        <li><svg viewBox="0 0 16 16" aria-hidden="true"><path d="M1 3h14v10H1zm1.5 1.5L8 9l5.5-4.5z"/></svg>dale@stonebr.com</li>
        <li><svg viewBox="0 0 16 16" aria-hidden="true"><circle cx="8" cy="8" r="7"/><path d="M4 5c2 0 2 2 4 2s1 3 3 3M9 2c0 2 3 2 4 4" stroke="#f3f3f3" stroke-width="1.4" fill="none"/></svg>www.stonebrace.ca</li>
      </ul>
    </div>
  </section>

  <section class="card card--back" aria-label="Card back">
    <div class="back-shape" role="img" aria-label="Large black brand pattern"></div>
    <div class="wordmark">THE STONEBRACE CO.</div>
    <div class="tagline">Crushing Solutions</div>
  </section>
</body>
</html>
```